Innovative cost reduction consultant needs to build a group of technical advisors

We need to share our message and compassion for developing cost reduction in the automotive industry. We create opportunities for immediate innovation, by developing cost reduction solutions across suppliers with related process. Attached is an existing Power Point, but it needs improvement. Most of all, a good compelling story, why experts should join us.

Target Market(s)

Automotive industry, supply chain management

Industry/Entity Type

Automotive

Font styles to use
Serif
Sans Serif

Requirements
Must have
• Better visual graphics. There are a few, but they are not as visually appearing as I would like. A graphic with data should have a better visual impact then the ones that I created. I would like to share the message, that I am providing a solution for the automotive industry. The goal is to reduce costs and improve supplier and OEM relationships. The objective is to do so by creating opportunities for immediate innovation, by developing cost reduction solutions across suppliers with related processes. This message may need a visual graphic, which is missing from the presentation.
Nice to have
• Challenge my story and presentation. Does this make sense to you, and what is your opinions of the subject. Or, a relevant news source to validate the story.
Should not have
• I have not decided on the name of the venture or logo. So, let's just use my name as the source or writer. Marcus Delby, Cost Reduction Specialist. Thanks,

```html
<!DOCTYPE html>
<html lang="en">
<head>
<meta charset="UTF-8">
<title>Conceptual Model</title>
<link href="https://fonts.googleapis.com/css2?family=Anton&family=Roboto+Condensed:wght@400;700&display=swap" rel="stylesheet">
<style>
  :root {
    --band-blue: #0b4fa3;
    --band-blue-deep: #083f8c;
    --strip-blue: #1ea3e8;
    --accent-blue: #2a9fe0;
    --dot-blue: #5fb8ea;
    --ink: #4a4a4a;
    --ink-soft: #3d3d3d;
    --white: #ffffff;
    --scene-light: #f3f6f8;
    --scene-mid: #c9d8e3;
    --scene-deep: #4f85ad;
  }
  * { margin: 0; padding: 0; box-sizing: border-box; }
  html, body { width: 1200px; height: 650px; overflow: hidden; background: var(--white); }
  .slide {
    position: relative;
    width: 1200px;
    height: 650px;
    overflow: hidden;
    font-family: "Roboto Condensed", "Arial Narrow", sans-serif;
  }
  .scene {
    position: absolute;
    left: 0; top: 172px;
    width: 1200px; height: 452px;
    background:
      radial-gradient(ellipse 420px 300px at 880px 360px, rgba(150,160,170,0.55), rgba(150,160,170,0) 70%),
      linear-gradient(100deg, var(--scene-light) 0%, var(--scene-light) 28%, var(--scene-mid) 58%, var(--scene-deep) 100%);
  }
  .title-band {
    position: absolute;
    left: 0; top: 0;
    width: 1200px; height: 172px;
    background: linear-gradient(180deg, var(--band-blue) 0%, var(--band-blue-deep) 100%);
  }
  .hand-area {
    position: absolute;
    left: 730px; top: 0;
    width: 370px; height: 330px;
    border-radius: 40% 40% 30% 30%;
    background: radial-gradient(ellipse at 55% 40%, rgba(226,190,165,0.95) 0%, rgba(214,176,150,0.8) 45%, rgba(214,176,150,0) 72%);
  }
  .slide-title {
    position: absolute;
    left: 96px; top: 70px;
    color: var(--white);
    font-weight: 700;
    font-size: 38px;
    letter-spacing: -0.3px;
  }
  .bottom-strip {
    position: absolute;
    left: 0; bottom: 0;
    width: 1200px; height: 26px;
    background: var(--strip-blue);
  }
  .connectors { position: absolute; left: 0; top: 0; }
  .input-box {
    position: absolute;
    left: 89px;
    width: 255px; height: 59px;
    background: var(--white);
    border: 1.5px dotted var(--dot-blue);
    border-radius: 6px;
    padding: 6px 12px;
  }
  .input-box h3 {
    font-size: 21px; font-weight: 700; color: var(--ink-soft); line-height: 1.1;
  }
  .input-box p {
    font-size: 17px; color: var(--ink); line-height: 1.2;
    display: flex; align-items: center; gap: 4px;
  }
  .input-box p::before {
    content: ""; width: 0; height: 0;
    border-top: 7px solid transparent; border-bottom: 7px solid transparent;
    border-left: 9px solid var(--accent-blue);
  }
  .box-model { top: 220px; }
  .box-value { top: 313px; }
  .box-business { top: 407px; }
  .hub {
    position: absolute;
    left: 435px; top: 304px;
    width: 132px; height: 132px;
    border-radius: 50%;
    background: var(--white);
    border: 1.5px dotted var(--dot-blue);
    display: flex; align-items: center; justify-content: center;
    text-align: center;
    font-size: 22px; font-weight: 700; color: var(--ink-soft); line-height: 1.2;
  }
  .headline {
    position: absolute;
    left: 618px; top: 252px;
    font-family: "Anton", "Impact", sans-serif;
    color: var(--white);
    text-shadow: 2px 3px 4px rgba(30,40,55,0.75);
    line-height: 0.9;
    text-transform: uppercase;
  }
  .headline span { display: block; }
  .headline .line-lead { font-size: 50px; letter-spacing: 0.5px; }
  .headline .line-key { font-size: 112px; margin-left: 52px; letter-spacing: 2px; }
  .headline .line-tail { font-size: 80px; margin-left: 52px; letter-spacing: 1px; }
</style>
</head>
<body>
<div class="slide">
  <div class="scene" role="img" aria-label="Row of white dollar-sign figures fading into a blue-grey background with a large metallic dollar sign"></div>
  <div class="title-band"></div>
  <div class="hand-area" role="img" aria-label="Hand lifting a metallic dollar sign"></div>
  <h1 class="slide-title">Conceptual Model</h1>

  <svg class="connectors" width="1200" height="650" viewBox="0 0 1200 650" aria-hidden="true">
    <g stroke="var(--dot-blue)" stroke-width="2" stroke-dasharray="2 3" fill="none" stroke-linecap="round">
      <path d="M344 228 L440 336"/><path d="M344 240 L442 340"/><path d="M344 252 L444 344"/><path d="M344 264 L446 348"/><path d="M344 276 L448 352"/>
      <path d="M344 322 L436 360"/><path d="M344 332 L436 364"/><path d="M344 342 L436 370"/><path d="M344 352 L436 376"/><path d="M344 362 L436 380"/>
      <path d="M344 415 L448 388"/><path d="M344 427 L446 392"/><path d="M344 439 L444 396"/><path d="M344 451 L442 400"/><path d="M344 463 L440 404"/>
    </g>
    <path d="M567 362 L640 362 L640 348 L664 370 L640 392 L640 378 L567 378 Z" fill="var(--white)"/>
  </svg>

  <div class="input-box box-model">
    <h3>New Model</h3>
    <p>Automaker/OEM</p>
  </div>
  <div class="input-box box-value">
    <h3>Added value</h3>
    <p>Supply Chain Management</p>
  </div>
  <div class="input-box box-business">
    <h3>Business Development</h3>
    <p>New Technology</p>
  </div>

  <div class="hub">Supplier<br>Dashboard</div>

  <h2 class="headline">
    <span class="line-lead">Innovative</span>
    <span class="line-key">Cost</span>
    <span class="line-tail">Reduction</span>
  </h2>

  <div class="bottom-strip"></div>
</div>
</body>
</html>
```